Web design for consulting advisory business company

We need a web for our business consulting company. The web should transmit simplicity, innovation, trust, and solid knowledge of what we do. Inspirational webs to take a look are: https://brindlemoor.com/ and http://tavunexa.com.br. Use blue colors.

Target Market(s)

Private companies

Industry/Entity Type

Management Consulting

Number of Pages Required

5+ page

Font styles to use
Serif
Sans Serif

Colors
3176b5
3276b5
85abd2
85cae6
33a6d7
0592cd
ffffff
1b1b1b
474747

Requirements
Must have
• - use of blue
• - images
• - same version in different languages (portugueses and spanish)
Nice to have
• - white as background

```html
<!DOCTYPE html>
<html lang="pt">
<head>
<meta charset="utf-8">
<title>Vantor Partners</title>
<link href="https://fonts.googleapis.com/css2?family=Montserrat:wght@600;700;800&family=Open+Sans:wght@400;600;700&display=swap" rel="stylesheet">
<style>
:root{
  --navy:#0c1a33;
  --blue:#1f7fd6;
  --blue-soft:#4c93dc;
  --green:#1e9a45;
  --green-dark:#177c37;
  --white:#ffffff;
  --ink:#1b1b1b;
  --grey:#474747;
  --line:#d5dbe3;
}
*{margin:0;padding:0;box-sizing:border-box}
html,body{width:1200px;height:4959px;overflow:hidden}
body{font-family:"Open Sans",Arial,sans-serif;color:var(--ink);background:var(--white);position:relative}
.abs{position:absolute}
h1,h2,h3{font-family:"Montserrat",Arial,sans-serif}

/* hero */
.hero{left:0;top:0;width:1200px;height:757px;background:linear-gradient(180deg,#0f1d3a 0%,#1d3460 45%,#14233f 70%,#0a1428 100%);color:var(--white)}
.brand{left:148px;top:52px;display:flex;align-items:center;gap:14px}
.brand-mark{width:50px;height:50px;border:0;background:var(--white);border-radius:4px}
.brand-name{font-family:"Montserrat",sans-serif;font-weight:700;font-size:34px;letter-spacing:1px;color:var(--white)}
.menu{left:822px;top:64px}
.lang{left:875px;top:56px;width:175px;height:44px;border:2px solid var(--white);border-radius:22px;font-size:17px;font-weight:600;display:flex;align-items:center;justify-content:center;gap:10px}
.hero h1{left:0;top:236px;width:1200px;text-align:center;font-size:60px;font-weight:800;letter-spacing:1px}
.hero .lead{left:300px;top:324px;width:600px;text-align:center;font-size:17px;line-height:28px}
.btn{display:flex;align-items:center;justify-content:center;border-radius:24px;font-weight:700;font-size:16px;text-transform:uppercase}
.btn-quote{left:393px;top:410px;width:195px;height:46px;border:2px solid var(--white)}
.btn-video{left:604px;top:410px;width:202px;height:46px;background:var(--blue);gap:14px}
.scroll{left:578px;top:570px}

/* feature rows */
.photo{width:600px;height:493px}
.panel{width:600px;color:var(--white);padding:80px 60px 0 58px}
.panel h2{font-size:38px;font-weight:700;margin-bottom:26px;text-transform:uppercase}
.panel p{font-size:15px;line-height:25px}
.panel.blue{background:var(--blue)}
.panel.green{background:var(--green)}
.more{display:inline-flex;margin-top:30px;height:38px;padding:0 24px;border:2px solid var(--white);border-radius:20px;align-items:center;font-size:14px;font-weight:700}
.cases li{list-style:none;display:flex;gap:16px;font-size:14px;line-height:23px;margin-top:18px}
.cases li svg{flex:none;margin-top:3px}

/* team */
.team h2{left:0;top:3042px;width:1200px;text-align:center;font-size:36px;font-weight:700}
.team-accent{left:150px;top:3135px;width:292px;height:20px;background:var(--blue)}
.team-card{left:150px;top:3148px;width:900px;height:384px;background:var(--white);border:2px solid var(--line);box-shadow:0 6px 18px rgba(0,0,0,.12)}
.team-photo{left:170px;top:3168px;width:286px;height:334px;background:linear-gradient(135deg,#6b5a48,#2c2a2a 60%,#8b98a6)}
.team-text{left:500px;top:3175px;width:520px}
.team-text h3{font-size:24px;font-weight:700;margin-bottom:20px}
.team-text p{font-size:14px;line-height:24px;color:var(--grey);margin-bottom:10px}
.team-text .more{border-color:var(--blue);color:var(--blue);margin-top:14px}
.arrow{top:3290px}

/* contact */
.contact{left:0;top:3662px;width:1200px;height:767px;background:var(--blue-soft);color:var(--white)}
.contact h2{position:absolute;top:88px;width:1200px;text-align:center;font-size:36px;font-weight:700}
.contact .intro{position:absolute;top:168px;left:280px;width:640px;text-align:center;font-size:15px;line-height:25px}
.field{position:absolute;left:165px;width:423px;height:38px;background:var(--white);color:var(--grey);font-size:14px;padding:9px 12px;border-radius:2px}
.field.msg{left:612px;top:353px;width:423px;height:202px}
.submit{position:absolute;left:488px;top:605px;width:220px;height:52px;background:var(--ink);color:var(--white);font-family:"Montserrat",sans-serif;font-size:22px;font-weight:700;display:flex;align-items:center;justify-content:center;border-radius:3px}

/* offices */
.offices{left:0;top:4429px;width:1200px;height:238px;background:var(--green)}
.office{position:absolute;top:66px;display:flex;gap:22px;color:var(--white)}
.office h3{font-size:20px;font-weight:700;margin-bottom:8px}
.office p{font-size:14px;line-height:22px;width:200px}

/* footer */
.foot-links{left:0;top:4726px;width:1200px;text-align:center;font-size:17px;color:var(--ink)}
.foot-copy{left:0;top:4774px;width:1200px;text-align:center;font-size:16px;color:var(--ink)}
.socials{left:532px;top:4834px;display:flex;gap:16px}
.socials span{width:36px;height:36px;border:2px solid var(--ink);border-radius:50%}
</style>
</head>
<body>

<header class="hero abs">
  <div class="abs" role="img" aria-label="Vista noturna de arranha-céus iluminados de uma cidade" style="inset:0;background:radial-gradient(ellipse at 80% 30%,rgba(120,150,200,.35),transparent 60%),radial-gradient(ellipse at 20% 80%,rgba(200,120,80,.25),transparent 55%)"></div>
  <div class="brand abs"><span class="brand-mark"></span><span class="brand-name">VANTOR PARTNERS</span></div>
  <svg class="menu abs" width="30" height="24" viewBox="0 0 30 24"><rect y="0" width="30" height="4" fill="#fff"/><rect y="10" width="30" height="4" fill="#fff"/><rect y="20" width="30" height="4" fill="#fff"/></svg>
  <div class="lang abs">Português <svg width="12" height="8" viewBox="0 0 12 8"><path d="M1 1l5 5 5-5" stroke="#fff" stroke-width="2" fill="none"/></svg></div>
  <h1 class="abs">VANTOR PARTNERS</h1>
  <p class="lead abs">Quis autem vel eum iure reprehenderit qui in ea voluptate velit esse quam nihil molestiae consequatur, vel illum qui dolorem eum fugiat quo</p>
  <div class="btn btn-quote abs">Request a quote</div>
  <div class="btn btn-video abs">Watch video <svg width="26" height="26" viewBox="0 0 26 26"><circle cx="13" cy="13" r="11" stroke="#fff" stroke-width="2" fill="none"/><path d="M10 8l8 5-8 5z" fill="#fff"/></svg></div>
  <svg class="scroll abs" width="44" height="90" viewBox="0 0 44 90"><rect x="9" y="2" width="26" height="46" rx="13" stroke="#fff" stroke-width="3" fill="none"/><rect x="20" y="12" width="4" height="10" rx="2" fill="#fff"/><path d="M12 60l10 8 10-8M12 72l10 8 10-8" stroke="#fff" stroke-width="3" fill="none"/></svg>
</header>

<section>
  <div class="photo abs" style="left:0;top:757px;background:linear-gradient(135deg,#c9a878,#f1e6d4 45%,#5d6f84)" role="img" aria-label="Mãos de profissional analisando gráficos e relatórios sobre a mesa"></div>
  <div class="panel blue abs" style="left:600px;top:757px;height:493px">
    <h2>Princípios</h2>
    <p>Adaptamos a equipe e os esforços para o problema, combinando recursos sêniores e especialistas do setor com fortes recursos analíticos para fornecer soluções sustentáveis. Ouvimos atentamente os nossos clientes e cerebramos as nossas equipes com as suas necessidades. Se o escopo do projeto mudar, mudamos a configuração. Pensamos na implementação desde</p>
    <span class="more">READ MORE</span>
  </div>
</section>

<section>
  <div class="panel green abs" style="left:0;top:1250px;height:495px">
    <h2>Expertise</h2>
    <p>Um núcleo de recursos sêniores, combinado com especialistas do setor, garante resultados sustentáveis para nossos clientes. Nós adaptamos a equipe e os esforços para cada situação e criamos impacto através de insights e orientação para as pessoas. Quando solicitado, nos juntamos a especialistas e pioneiros de todos os cantos do mundo.</p>
    <span class="more">READ MORE</span>
  </div>
  <div class="photo abs" style="left:600px;top:1250px;height:495px;background:linear-gradient(135deg,#8fb7d8,#e9eef2 50%,#4c6f92)" role="img" aria-label="Equipe de consultores conversando em reunião com laptops"></div>
</section>

<section>
  <div class="photo abs" style="left:0;top:1745px;height:701px;background:linear-gradient(135deg,#2b2f36,#6d7784 50%,#d8dde2)" role="img" aria-label="Pessoa usando laptop com painel de gráficos na tela"></div>
  <div class="panel blue abs" style="left:600px;top:1745px;height:701px">
    <h2>Cases</h2>
    <p>A nossa equipe sênior tem ampla experiência em projetos de alto impacto. Algumas dessas experiências incluem:</p>
    <ul class="cases">
      <li><svg width="18" height="18" viewBox="0 0 18 18"><circle cx="9" cy="9" r="8" stroke="#fff" stroke-width="1.5" fill="none"/><path d="M5 9l3 3 5-6" stroke="#fff" stroke-width="1.8" fill="none"/></svg><span>Identificação das principais sinergias, elaboração do modelo de negócios e do plano de integração de duas Grandes Instituições Financeiras Brasileiras; coordenação e acompanhamento da implementação do PMO</span></li>
      <li><svg width="18" height="18" viewBox="0 0 18 18"><circle cx="9" cy="9" r="8" stroke="#fff" stroke-width="1.5" fill="none"/><path d="M5 9l3 3 5-6" stroke="#fff" stroke-width="1.8" fill="none"/></svg><span>Desenvolvimento do orçamento anual e plano de investimento trienal para Grande Empresa Brasileira de Serviços Financeiros, identificando oportunidades de melhoria de 9% do orçamento total</span></li>
      <li><svg width="18" height="18" viewBox="0 0 18 18"><circle cx="9" cy="9" r="8" stroke="#fff" stroke-width="1.5" fill="none"/><path d="M5 9l3 3 5-6" stroke="#fff" stroke-width="1.8" fill="none"/></svg><span>Reestruturação da organização de vendas e revisão das políticas comerciais de Empresas Farmacêuticas e de Mídia Online com operações no Brasil</span></li>
    </ul>
    <span class="more">READ MORE</span>
  </div>
</section>

<section>
  <div class="panel green abs" style="left:0;top:2446px;height:495px">
    <h2>Ecosistema</h2>
    <p>Nos juntamos a especialistas globais e pioneiros de todo o mundo. A necessidade de velocidade e complexidade de problemas exige uma abordagem flexível, e nosso ecossistema oferece acesso a conhecimento exclusivo de líderes da indústria de classe mundial.</p>
    <span class="more">READ MORE</span>
  </div>
  <div class="photo abs" style="left:600px;top:2446px;height:495px;background:linear-gradient(135deg,#c5ced8,#f4f5f6 45%,#6a7686)" role="img" aria-label="Executivos em reunião de negócios analisando documentos"></div>
</section>

<section class="team">
  <h2 class="abs">EQUIPE SÊNIOR</h2>
  <svg class="arrow abs" style="left:92px" width="20" height="34" viewBox="0 0 20 34"><path d="M17 2L3 17l14 15" stroke="#474747" stroke-width="2.5" fill="none"/></svg>
  <svg class="arrow abs" style="left:1088px" width="20" height="34" viewBox="0 0 20 34"><path d="M3 2l14 15L3 32" stroke="#474747" stroke-width="2.5" fill="none"/></svg>
  <div class="team-accent abs"></div>
  <div class="team-card abs"></div>
  <div class="team-photo abs" role="img" aria-label="Retrato de consultor sênior trabalhando no laptop"></div>
  <div class="team-text abs">
    <h3>TOMÁS ARRIEL</h3>
    <p>Administrador de Empresas pela Universidade Austral do Prata (UAP) e Master em Business Administration (MBA) pela Halden School of Management at Northgate University (EUA).</p>
    <p>Tem atuado como consultor de negócios nas áreas de planejamento estratégico, eficiência organizacional, marketing e vendas, avaliação de novos negócios, reestruturação de operações, fusões e aquisições, para empresas como Bravan, Solcor, Teranova, Lumedi, Verdana, Conecta e Pedralta.</p>
    <span class="more">READ MORE</span>
  </div>
</section>

<section class="contact abs">
  <h2>CONTATO</h2>
  <p class="intro">Frase: Avance com confiança.<br>Contate-nos para mais informações sobre como Vantor Partners pode ajudar você a conseguir melhores resultados, otimizar o desempenho e melhorar o crescimento do seu negócio.<br><br>Utilize o formulário de contato abaixo ou envie-nos um e-mail diretamente a<br><u>contato@vantor-partners.com.br</u></p>
  <div class="field" style="top:368px">Nome</div>
  <div class="field" style="top:424px">Organização</div>
  <div class="field" style="top:478px">Telefone</div>
  <div class="field" style="top:534px">E-mail</div>
  <div class="field msg">Mensagem</div>
  <div class="submit">SUBMIT</div>
</section>

<section class="offices abs">
  <div class="office" style="left:150px">
    <svg width="44" height="44" viewBox="0 0 44 44"><circle cx="22" cy="22" r="20" stroke="#fff" stroke-width="2" fill="none"/><path d="M22 11a7 7 0 0 0-7 7c0 5 7 13 7 13s7-8 7-13a7 7 0 0 0-7-7z" fill="#fff"/><circle cx="22" cy="18" r="2.6" fill="#1e9a45"/></svg>
    <div><h3>Rio de Janeiro</h3><p>Av. Atlântida, 418 – 9º andar – Centro Rio de Janeiro | 20031-210 | RJ</p></div>
  </div>
  <div class="office" style="left:462px">
    <svg width="44" height="44" viewBox="0 0 44 44"><circle cx="22" cy="22" r="20" stroke="#fff" stroke-width="2" fill="none"/><path d="M22 11a7 7 0 0 0-7 7c0 5 7 13 7 13s7-8 7-13a7 7 0 0 0-7-7z" fill="#fff"/><circle cx="22" cy="18" r="2.6" fill="#1e9a45"/></svg>
    <div><h3>São Paulo</h3><p>Rua Alvorada Norte, 315 – Bloco B, 6º andar – Vila Nova São Paulo | 04552-110 | SP</p></div>
  </div>
  <div class="office" style="left:788px">
    <svg width="44" height="44" viewBox="0 0 44 44"><circle cx="22" cy="22" r="20" stroke="#fff" stroke-width="2" fill="none"/><path d="M22 11a7 7 0 0 0-7 7c0 5 7 13 7 13s7-8 7-13a7 7 0 0 0-7-7z" fill="#fff"/><circle cx="22" cy="18" r="2.6" fill="#1e9a45"/></svg>
    <div><h3>Buenos Aires</h3><p>Calle Ribera Sur 1870 – Olivos Buenos Aires | B1637 AKP | Argentina</p></div>
  </div>
</section>

<footer>
  <p class="foot-links abs">Princípios &nbsp;|&nbsp; Expertise &nbsp;|&nbsp; Cases &nbsp;|&nbsp; Ecosistema &nbsp;|&nbsp; Equipe Sênior &nbsp;|&nbsp; Contato</p>
  <p class="foot-copy abs">Vantor Partners © 2019 All Rights Reserved | term and condition</p>
  <div class="socials abs"><span></span><span></span><span></span></div>
</footer>

</body>
</html>
```